Website for Dental Office - The Bright Arch Clinic

The bright arch clinic is a dental office offering cosmetic dentistry, general dentistry, and multi-specialty dental care all under one roof in our state-of-the-art cosmetic dental center. We are particularly striving to provide services that fit the need of the young generation. Thus, we hope to have a modern, professional concise website that represents our spirit.

*Should be able to switch from English to Chinese

6 sections besides homepage:
Home, Meet us, Services,
Patient Info, Cases&Reviews, Blog, Contact

The Services sections should contain multiple subsections such as cleaning and prevention, cosmetic dentistry, implant dentistry, removable dentures, etc...
The Patient Info section is also intended to contain several subsections such as
New Patient offer, accepted Insurance, patient portal, helpful tips, etc...

Target Market(s)

young generation

Coding

Coded - Design and coding required

Number of Pages Required

5+ page

Font styles to use
Sans Serif

Colors
0592cd
33a6d7
85cae6
00a990
33b8a4
86cfc6
cee9f5
cfeae6
3277b5

Requirements
Must have
• *Should be able to switch from English to Chinese
Nice to have
• http://www.thebrightarchclinic.com/
• As a reference, the above link is the current website, but we would like to change the appearance and the content (our new logo's picture is attached)

```html
<!DOCTYPE html>
<html lang="en">
<head>
<meta charset="utf-8">
<title>The Bright Arch Clinic</title>
<link href="https://fonts.googleapis.com/css2?family=Montserrat:wght@400;500;600;700&family=Great+Vibes&display=swap" rel="stylesheet">
<style>
:root{
  --blue:#0592cd;--blue-2:#33a6d7;--blue-3:#85cae6;--blue-pale:#cee9f5;
  --green:#00a990;--green-card:#17997b;--green-2:#33b8a4;--green-3:#86cfc6;--green-pale:#cfeae6;
  --navy:#3277b5;--royal:#2a63ad;--ink:#1d1d1d;--text:#444;--grey-band:#f3f3f3;--white:#fff;
}
*{box-sizing:border-box;margin:0;padding:0}
html,body{width:1200px;height:3535px;overflow:hidden}
body{position:relative;font-family:'Montserrat',sans-serif;color:var(--text);background:var(--white)}
.abs{position:absolute}
a{color:inherit;text-decoration:none}

/* header */
.topline{right:72px;top:15px;font-size:14px;color:#333}
.phone{right:72px;top:40px;font-size:29px;font-weight:600;color:#222;letter-spacing:1px;display:flex;align-items:center;gap:16px}
.nav{top:104px;font-size:15px;color:#333;display:flex;gap:40px}
.nav .active{color:var(--blue);position:relative}
.nav .active::after{content:"";position:absolute;left:-14px;right:-14px;top:33px;height:3px;background:var(--blue)}
.logo{left:500px;top:0;width:200px;height:172px}
.logo-name{position:absolute;left:0;right:0;top:115px;text-align:center;font-size:15px;font-weight:700;color:var(--blue)}

/* hero */
.hero{left:0;top:150px;width:1200px;height:556px;background:linear-gradient(110deg,#d7e8ee 0%,#c4dfe7 45%,#cfe3ea 70%,#e4eef0 100%)}
.hero-inner{position:absolute;left:0;right:0;top:195px;text-align:center}
.script{font-family:'Great Vibes',cursive;font-size:36px;color:#333}
.hero h1{font-size:35px;font-weight:600;color:#1b1b1b;margin-top:6px}
.hero p{font-size:16.5px;line-height:27.5px;color:#333;width:650px;margin:12px auto 0}
.btn{display:inline-block;height:42px;line-height:42px;border-radius:21px;color:#fff;font-size:15px;font-weight:600;letter-spacing:1.5px;padding:0 26px}
.btn-green{background:var(--green-card)}
.btn-royal{background:var(--royal);padding:0 32px}
.hero-btns{margin-top:22px;display:flex;justify-content:center;gap:24px}
.round-arrow{width:46px;height:46px;border-radius:50%;background:rgba(80,80,80,.6);display:flex;align-items:center;justify-content:center}

.band{left:0;top:706px;width:1200px;height:104px;background:var(--grey-band)}
.card{width:335px;height:320px}
.card-title{position:absolute;left:0;right:0;top:132px;text-align:center;color:#fff;font-size:22px;font-weight:700;line-height:26px}
.card-text{position:absolute;left:0;right:0;top:200px;text-align:center;color:#e9f4f1;font-size:14px;line-height:27.5px}

.divider{left:66px;top:1060px;width:1066px;height:1px;background:#d8d8d8}

/* offer */
.offer-photo{left:68px;top:1122px;width:517px;height:318px;background:linear-gradient(100deg,#9fc0dc 0%,#dfe9f0 50%,#c9d8e2 100%);overflow:hidden;box-shadow:0 0 8px rgba(0,0,0,.12)}
.offer h2{font-size:29px;font-weight:600;color:#1b1b1b}
.offer p{font-size:14.5px;line-height:27.5px;color:#444;margin-top:22px}
.offer .more{display:inline-block;margin-top:30px;font-size:14.5px;font-weight:600;color:var(--royal);text-decoration:underline}

/* about */
.about{left:0;top:1552px;width:1200px;height:573px;background:linear-gradient(120deg,#2678ae,#2d86b9 50%,#2a7ab1)}
.about h2{position:absolute;left:0;right:0;top:60px;text-align:center;color:#fff;font-weight:400;font-size:32px}
.about .lead{position:absolute;left:105px;right:105px;top:115px;text-align:center;color:#e6f1f7;font-size:16.5px;line-height:27.5px}
.tile{top:216px;width:242px}
.tile-img{height:160px;width:242px}
.tile-label{margin-top:18px;text-align:center;color:#fff;font-size:17.5px;font-weight:700}
.brand-box{background:#fff;display:flex;align-items:center;justify-content:center;font-size:30px;font-weight:600;color:var(--royal)}
.side-arrow{width:35px;height:42px;background:var(--green-card);display:flex;align-items:center;justify-content:center}

/* team */
.team-title{left:0;right:0;top:2180px;text-align:center;font-size:31px;color:#222}
.team-title b{font-weight:700}
.member{top:2290px;height:250px}
.member-name{font-size:14px;font-weight:700;letter-spacing:1.5px;color:#222;line-height:25px;margin-top:14px;padding-left:8px}
.member-feature{left:354px;top:2265px;width:260px;height:300px;background:#b9b9b9;box-shadow:0 4px 12px rgba(0,0,0,.25)}
.member-feature .name{position:absolute;left:20px;bottom:30px;font-size:21px;font-weight:700;letter-spacing:2px;color:#222;line-height:25px}
.sq-arrow{width:40px;height:42px;display:flex;align-items:center;justify-content:center}

/* testimonials */
.testi{left:0;top:2622px;width:1200px;height:480px;background:linear-gradient(120deg,#3b6fb8,#4378bd 50%,#3a6db5)}
.testi h2{position:absolute;left:0;right:0;top:120px;text-align:center;color:#fff;font-size:30px;font-weight:600}
.quote-box{left:140px;top:185px;width:904px;height:181px;background:#fff}
.quote{position:absolute;left:218px;top:32px;width:640px;font-size:17.5px;line-height:28px;color:#333}
.stars{position:absolute;left:218px;top:100px;display:flex;gap:9px}
.author{position:absolute;left:218px;top:130px;font-size:18px;font-weight:700;color:#222}

/* footer */
.f-title{font-size:29px;font-weight:500;color:#1b1b1b}
.links{list-style:none;margin-top:22px}
.links li{font-size:13px;color:#333;height:33.5px;display:flex;align-items:center;gap:14px}
.email-field{width:332px;height:42px;background:#eeeeee;display:flex;align-items:center;justify-content:space-between;padding:0 20px 0 18px;font-size:15px;color:#333;margin-top:24px}
.social{display:flex;gap:22px;margin-top:28px}
.social span{width:20px;height:20px;border-radius:50%;border:2px solid #333;display:inline-block}
.contact-row{display:flex;gap:22px;font-size:15.5px;line-height:25px;color:#333}
.foot-bar{left:0;top:3478px;width:1200px;height:57px;background:var(--royal);color:#fff;font-size:14px;font-weight:600;text-align:center;line-height:57px}
</style>
</head>
<body>

<header>
  <div class="abs topline">✉ hello@brightarchdental.com</div>
  <div class="abs phone">
    <svg width="20" height="20" viewBox="0 0 24 24"><path d="M6.6 10.8a15 15 0 0 0 6.6 6.6l2.2-2.2c.3-.3.7-.4 1-.2 1.1.4 2.3.6 3.6.6.6 0 1 .4 1 1V20c0 .6-.4 1-1 1A17 17 0 0 1 3 4c0-.6.4-1 1-1h3.5c.6 0 1 .4 1 1 0 1.3.2 2.5.6 3.6.1.3 0 .7-.2 1z" fill="#222"/></svg>
    1-800 555 0142
  </div>
  <nav class="abs nav" style="left:70px">
    <a class="active">Home</a><a>Meet us</a><a>Services</a><a>Patient Info</a>
  </nav>
  <nav class="abs nav" style="left:759px">
    <a>Cases&amp;Reviews</a><a>Blog</a><a>Contact</a>
  </nav>
  <svg class="abs" style="left:1110px;top:106px" width="16" height="16" viewBox="0 0 16 16"><circle cx="6.5" cy="6.5" r="5" fill="none" stroke="#222" stroke-width="2"/><path d="M10 10l4.5 4.5" stroke="#222" stroke-width="2.4"/></svg>
</header>

<section class="abs hero" role="img" aria-label="Smiling woman and young girl at a dental office">
  <div class="hero-inner">
    <div class="script">Lorium ipsum</div>
    <h1>The bright arch clinic</h1>
    <p>Is a dental office offering cosmetic dentistry general dentistry, and multi-specialty dental care all under one roof in our state-of-the-art cosmetic dental center.</p>
    <div class="hero-btns"><a class="btn btn-green">LEARN MORE</a><a class="btn btn-royal">BOOK APPOINTMENT</a></div>
  </div>
  <div class="abs round-arrow" style="left:111px;top:249px"><svg width="12" height="14"><path d="M8 2L3 7l5 5" stroke="#fff" stroke-width="2.5" fill="none"/></svg></div>
  <div class="abs round-arrow" style="left:1037px;top:249px"><svg width="12" height="14"><path d="M4 2l5 5-5 5" stroke="#fff" stroke-width="2.5" fill="none"/></svg></div>
</section>

<div class="abs logo">
  <svg width="200" height="172" viewBox="0 0 200 172">
    <path d="M0 150 H70 L100 172 L130 150 H200 V0 H0 Z" fill="#fff"/>
    <rect x="85" y="50" width="30" height="30" fill="var(--blue)"/>
  </svg>
  <div class="logo-name">THE BRIGHT ARCH CLINIC</div>
</div>

<div class="abs band"></div>

<div class="abs card" style="left:70px;top:672px">
  <svg width="335" height="320" viewBox="0 0 335 320"><circle cx="167" cy="75" r="75" fill="var(--green-card)"/><path d="M0 66 H335 V311 Q167 240 0 311 Z" fill="var(--green-card)"/><path d="M167 296v22M156 307h22" stroke="var(--green-card)" stroke-width="1.6"/></svg>
  <div class="card-title">CLEANING AND<br>PREVENTION</div>
  <div class="card-text">Lorem ipsum dolor sit amet,<br>consectetur adipiscing.</div>
</div>
<div class="abs card" style="left:433px;top:672px">
  <svg width="335" height="320" viewBox="0 0 335 320"><circle cx="167" cy="75" r="75" fill="var(--royal)"/><path d="M0 66 H335 V311 Q167 240 0 311 Z" fill="var(--royal)"/><path d="M167 296v22M156 307h22" stroke="var(--royal)" stroke-width="1.6"/></svg>
  <div class="card-title">COSMETIC<br>DENTISTRY</div>
  <div class="card-text">Lorem ipsum dolor sit amet,<br>consectetur adipiscing.</div>
</div>
<div class="abs card" style="left:794px;top:672px">
  <svg width="335" height="320" viewBox="0 0 335 320"><circle cx="167" cy="75" r="75" fill="var(--green-card)"/><path d="M0 66 H335 V311 Q167 240 0 311 Z" fill="var(--green-card)"/><path d="M167 296v22M156 307h22" stroke="var(--green-card)" stroke-width="1.6"/></svg>
  <div class="card-title">IMPLANT<br>DENTISTRY</div>
  <div class="card-text">Lorem ipsum dolor sit amet,<br>consectetur adipiscing.</div>
</div>

<div class="abs divider"></div>

<section>
  <div class="abs offer-photo" role="img" aria-label="Smiling dentist and patient">
    <svg class="abs" style="left:0;bottom:0" width="517" height="60" viewBox="0 0 517 60"><path d="M0 60 V48 Q258 -30 517 48 V60 Z" fill="#fff"/></svg>
  </div>
  <div class="abs offer" style="left:617px;top:1142px;width:480px">
    <h2>New Patient offer</h2>
    <p>Lorem ipsum dolor sit amet, consectetur adipiscing elit, sed do eiusmod tempor incididunt ut labore et dolore magna aliqua. Ut enim ad minim veniam, quis nostrud exercitation ullamco laboris nisi ut aliquip ex ea commodo consequat. Duis aute irure dolor in reprehenderit in voluptate velit</p>
    <a class="more">Read More</a>
  </div>
</section>

<section class="abs about">
  <h2>About The Patients</h2>
  <p class="lead">Lorem ipsum dolor sit amet, consectetur adipiscing elit, sed do eiusmod tempor incididunt ut labore et dolore magna aliqua. Ut enim ad minim veniam, quis nostrud exercitation ullamco laboris nisi.</p>
  <div class="abs tile" style="left:70px"><div class="tile-img" role="img" aria-label="Patient in a dental chair" style="background:linear-gradient(120deg,#e9eef1,#b9cbd6)"></div><div class="tile-label">PATIENT INFO</div></div>
  <div class="abs tile" style="left:342px"><div class="tile-img" role="img" aria-label="Dental check-up close view" style="background:linear-gradient(120deg,#d7b3a4,#9c5a4e)"></div><div class="tile-label">ACCEPTED INSURANCE</div></div>
  <div class="abs tile" style="left:614px"><div class="tile-img brand-box">CarePlan Pay</div><div class="tile-label">PATIENT PORTAL</div></div>
  <div class="abs tile" style="left:886px"><div class="tile-img" role="img" aria-label="Patient with mirror after treatment" style="background:linear-gradient(120deg,#8fa6b3,#d9dcdc)"></div><div class="tile-label">HELPFUL TIPS</div></div>
  <div class="abs side-arrow" style="left:0;top:307px"><svg width="10" height="14"><path d="M7 2L2 7l5 5" stroke="#fff" stroke-width="2.5" fill="none"/></svg></div>
  <div class="abs side-arrow" style="left:1165px;top:307px"><svg width="10" height="14"><path d="M3 2l5 5-5 5" stroke="#fff" stroke-width="2.5" fill="none"/></svg></div>
  <a class="abs btn btn-green" style="left:523px;top:470px;height:40px;line-height:40px;padding:0 32px">VIEW MORE</a>
</section>

<section>
  <h2 class="abs team-title" style="font-weight:400">Meet <b>Us</b></h2>
  <div class="abs sq-arrow" style="left:104px;top:2394px;background:var(--green-card)"><svg width="10" height="14"><path d="M7 2L2 7l5 5" stroke="#fff" stroke-width="2.5" fill="none"/></svg></div>
  <div class="abs sq-arrow" style="left:1056px;top:2394px;background:var(--green-3)"><svg width="10" height="14"><path d="M3 2l5 5-5 5" stroke="#fff" stroke-width="2.5" fill="none"/></svg></div>
  <div class="abs member" style="left:144px;width:210px"><div role="img" aria-label="Portrait of Nadia Ferro" style="height:250px;background:linear-gradient(#3a2a24,#1a1a1a)"></div><div class="member-name">NADIA FERRO,<br>DMD, MS</div></div>
  <div class="abs member-feature" role="img" aria-label="Portrait of Victor L. Hale"><div class="name">VICTOR L.<br>HALE DMD</div></div>
  <div class="abs member" style="left:614px;width:210px"><div role="img" aria-label="Portrait of Dr. Sara Nouri" style="height:250px;background:linear-gradient(#e8e8e6,#cfc9c4)"></div><div class="member-name" style="margin-top:8px">DR. SARA NOURI, DMD</div></div>
  <div class="abs member" style="left:839px;width:217px"><div role="img" aria-label="Portrait of Mila Okafor" style="height:250px;background:linear-gradient(#3c3430,#5a4a40)"></div><div class="member-name" style="padding-left:0">MILA OKAFOR</div></div>
</section>

<section class="abs testi">
  <h2>TESTIMONIALS</h2>
  <div class="abs quote-box">
    <div class="abs" role="img" aria-label="Portrait of Renata" style="left:52px;top:22px;width:140px;height:140px;border-radius:50%;background:radial-gradient(#c77a5a,#7a2f22);border:4px solid #fff;box-shadow:0 0 8px rgba(0,0,0,.3)"></div>
    <p class="quote">“Ut enim ad minima veniam, quis nostrum exercitationem ullam corporis suscipit laboriosam, nisi ut aliquid.</p>
    <div class="stars">
      <svg width="14" height="14" viewBox="0 0 24 24"><path d="M12 2l3 7h7l-5.5 4.5 2 7.5-6.5-4.5-6.5 4.5 2-7.5L2 9h7z" fill="var(--royal)"/></svg>
      <svg width="14" height="14" viewBox="0 0 24 24"><path d="M12 2l3 7h7l-5.5 4.5 2 7.5-6.5-4.5-6.5 4.5 2-7.5L2 9h7z" fill="var(--royal)"/></svg>
      <svg width="14" height="14" viewBox="0 0 24 24"><path d="M12 2l3 7h7l-5.5 4.5 2 7.5-6.5-4.5-6.5 4.5 2-7.5L2 9h7z" fill="var(--royal)"/></svg>
      <svg width="14" height="14" viewBox="0 0 24 24"><path d="M12 2l3 7h7l-5.5 4.5 2 7.5-6.5-4.5-6.5 4.5 2-7.5L2 9h7z" fill="var(--royal)"/></svg>
      <svg width="14" height="14" viewBox="0 0 24 24"><path d="M12 2l3 7h7l-5.5 4.5 2 7.5-6.5-4.5-6.5 4.5 2-7.5L2 9h7z" fill="var(--green-card)"/></svg>
    </div>
    <div class="author">- Renata</div>
  </div>
  <svg class="abs" style="left:574px;top:424px" width="52" height="34"><path d="M18 2L4 17l14 15M34 2l14 15-14 15" stroke="#fff" stroke-width="1.5" fill="none"/></svg>
</section>

<footer>
  <div class="abs" style="left:70px;top:3148px">
    <h3 class="f-title">Quick Links</h3>
    <ul class="links">
      <li>›&nbsp;<span>Home</span></li><li>›&nbsp;<span>Meet us</span></li><li>›&nbsp;<span>Services</span></li><li>›&nbsp;<span>Patient Info</span></li><li>›&nbsp;<span>Cases&amp;Reviews</span></li><li>›&nbsp;<span>Blog</span></li><li>›&nbsp;<span>Contact Us</span></li>
    </ul>
  </div>
  <div class="abs" style="left:435px;top:3148px">
    <h3 class="f-title">Newsletter Subscribe</h3>
    <div class="email-field">Enter Email id <span style="font-size:14px">✉</span></div>
    <a class="btn btn-green" style="margin-top:20px;height:42px;padding:0 33px">SUBSCRIBE</a>
    <div class="social"><span></span><span></span><span></span></div>
  </div>
  <div class="abs" style="left:876px;top:3148px">
    <h3 class="f-title">Contact us</h3>
    <div class="contact-row" style="margin-top:30px">
      <svg width="12" height="16" viewBox="0 0 12 16" style="margin-top:4px"><path d="M6 0a6 6 0 0 0-6 6c0 4.5 6 10 6 10s6-5.5 6-10a6 6 0 0 0-6-6zm0 8.5A2.5 2.5 0 1 1 6 3.5a2.5 2.5 0 0 1 0 5z" fill="#222"/></svg>
      <span>412 Maplewood Ave.<br>Cedar Falls, OH 44790</span>
    </div>
    <div class="contact-row" style="margin-top:22px">
      <svg width="14" height="14" viewBox="0 0 24 24" style="margin-top:5px"><path d="M6.6 10.8a15 15 0 0 0 6.6 6.6l2.2-2.2c.3-.3.7-.4 1-.2 1.1.4 2.3.6 3.6.6.6 0 1 .4 1 1V20c0 .6-.4 1-1 1A17 17 0 0 1 3 4c0-.6.4-1 1-1h3.5c.6 0 1 .4 1 1 0 1.3.2 2.5.6 3.6.1.3 0 .7-.2 1z" fill="#222"/></svg>
      <span>1-800 555 0178</span>
    </div>
    <div class="contact-row" style="margin-top:16px">
      <svg width="14" height="12" viewBox="0 0 14 12" style="margin-top:7px"><rect x="1" y="1" width="12" height="10" fill="none" stroke="#222" stroke-width="1.4"/><path d="M1 1l6 5 6-5" fill="none" stroke="#222" stroke-width="1.4"/></svg>
      <span>care@brightarchdental.com</span>
    </div>
    <div style="display:flex;align-items:center;gap:14px;margin-top:36px">
      <span style="width:40px;height:40px;background:var(--blue);display:inline-block"></span>
      <span style="font-size:21px;font-weight:600;color:var(--blue);line-height:25px">THE BRIGHT<br>ARCH CLINIC</span>
    </div>
  </div>
  <div class="abs foot-bar">© 2019 &nbsp;|&nbsp; www.brightarchdental.com</div>
</footer>

</body>
</html>
```